Poster

I need a poster for my business, www.coastalsupperroutesnerja.example which some information about the most important activities (Sangria Tasting, Iberian Ham, Charcuteries & Sherry Wine Tasting, Sailboat Experiences and Picnic Experiences). A3 Format. Social media included (@coastalsupperroutescsr), contact information included.

```html
<!DOCTYPE html>
<html lang="en">
<head>
<meta charset="utf-8">
<title>Coastal Supper Routes Nerja – Poster</title>
<link href="https://fonts.googleapis.com/css2?family=Bebas+Neue&family=Poppins:wght@600&display=swap" rel="stylesheet">
<style>
  :root {
    --poster-red: #c8101f;
    --ring-orange: #f2a516;
    --ink: #111111;
    --logo-grey: #555555;
    --paper: #ffffff;
    --divider: #d9d9d9;
  }
  html, body { margin: 0; padding: 0; overflow: hidden; }
  body { width: 880px; height: 1200px; background: var(--poster-red); }
  .poster { position: relative; width: 880px; height: 1200px; background: var(--poster-red); overflow: hidden; }
  .poster-art { position: absolute; inset: 0; }
  .brand-name {
    position: absolute; left: 300px; top: 404px; width: 282px;
    text-align: center; margin: 0;
    font-family: "Bebas Neue", "Arial Narrow", sans-serif;
    font-weight: 400; font-size: 38px; line-height: 36px;
    color: var(--logo-grey); letter-spacing: 0.5px;
  }
  .activities-title {
    position: absolute; left: 214px; top: 838px; width: 456px; margin: 0;
    text-align: center; color: var(--paper);
    font-family: "Bebas Neue", "Arial Narrow", sans-serif;
    font-weight: 400; font-size: 46px; line-height: 46px;
  }
  .activity {
    position: absolute; margin: 0; display: flex; align-items: center; gap: 18px;
    font-family: "Bebas Neue", "Arial Narrow", sans-serif;
    font-weight: 400; font-size: 45px; line-height: 45px; color: var(--ink);
    white-space: nowrap;
  }
  .activity svg { width: 17px; height: 26px; flex: none; }
  .contact {
    position: absolute; margin: 0; display: flex; align-items: center; gap: 10px;
    font-family: "Poppins", Arial, sans-serif; font-weight: 600;
    font-size: 18.5px; line-height: 28px; color: var(--paper); white-space: nowrap;
  }
  .contact svg { width: 24px; height: 24px; flex: none; }
</style>
</head>
<body>
<main class="poster">
  <svg class="poster-art" viewBox="0 0 880 1200" width="880" height="1200">
    <defs>
      <linearGradient id="tone-tapas" x1="0" y1="0" x2="1" y2="1">
        <stop offset="0" stop-color="#9fb3bd"/><stop offset="0.6" stop-color="#b58a64"/><stop offset="1" stop-color="#8c3b35"/>
      </linearGradient>
      <linearGradient id="tone-sangria" x1="0" y1="0" x2="1" y2="1">
        <stop offset="0" stop-color="#3a2a22"/><stop offset="0.5" stop-color="#7a2a26"/><stop offset="1" stop-color="#b59a86"/>
      </linearGradient>
      <linearGradient id="tone-board" x1="0" y1="0" x2="1" y2="1">
        <stop offset="0" stop-color="#6b5240"/><stop offset="0.5" stop-color="#d8c3a0"/><stop offset="1" stop-color="#7c5a45"/>
      </linearGradient>
      <linearGradient id="tone-sail" x1="0" y1="0" x2="0" y2="1">
        <stop offset="0" stop-color="#6aa3d8"/><stop offset="0.45" stop-color="#2a5f8c"/><stop offset="1" stop-color="#3b3a3a"/>
      </linearGradient>
      <linearGradient id="tone-picnic" x1="0" y1="0" x2="0" y2="1">
        <stop offset="0" stop-color="#4f7a3a"/><stop offset="0.45" stop-color="#eeeae6"/><stop offset="1" stop-color="#d6c3b8"/>
      </linearGradient>
    </defs>

    <g class="photo-rings" fill="var(--ring-orange)">
      <circle cx="441" cy="190" r="162"/>
      <circle cx="201" cy="383" r="160"/>
      <circle cx="692" cy="383" r="160"/>
      <circle cx="296" cy="622" r="160"/>
      <circle cx="592" cy="622" r="160"/>
    </g>

    <g class="photo-circles">
      <g role="img" aria-label="Photo: sangria glass with orange slice on a stone surface">
        <circle cx="201" cy="383" r="144" fill="url(#tone-sangria)"/>
      </g>
      <g role="img" aria-label="Photo: a couple on a sailboat deck at sea with the coast behind">
        <circle cx="296" cy="622" r="144" fill="url(#tone-sail)"/>
      </g>
      <g role="img" aria-label="Photo: outdoor picnic table set with glasses, plates and flowers">
        <circle cx="592" cy="622" r="144" fill="url(#tone-picnic)"/>
      </g>
      <g role="img" aria-label="Photo: charcuterie board with cheeses, crackers, olives and jam">
        <circle cx="692" cy="383" r="144" fill="url(#tone-board)"/>
      </g>
      <g role="img" aria-label="Photo: sliced Iberian ham, olives and a glass of sherry wine">
        <circle cx="441" cy="190" r="146" fill="url(#tone-tapas)"/>
      </g>
    </g>

    <circle class="brand-disc" cx="441" cy="440" r="156" fill="var(--paper)"/>

    <g class="activities-panel">
      <rect x="52" y="884" width="780" height="196" rx="30" fill="var(--paper)" stroke="var(--ring-orange)" stroke-width="6"/>
      <path class="title-tab" d="M196 884 C214 884 218 866 224 852 C230 838 238 834 256 834 L628 834 C646 834 654 838 660 852 C666 866 670 884 688 884"
            fill="var(--ink)" stroke="var(--ring-orange)" stroke-width="6" stroke-linejoin="round"/>
      <rect x="212" y="878" width="460" height="10" fill="var(--ink)"/>
      <line x1="85" y1="954" x2="795" y2="954" stroke="var(--divider)" stroke-width="1.5"/>
      <line x1="85" y1="1012" x2="795" y2="1012" stroke="var(--divider)" stroke-width="1.5"/>
    </g>
  </svg>

  <h1 class="brand-name">Coastal Supper<br>Routes Nerja</h1>

  <h2 class="activities-title">Important Activities</h2>

  <p class="activity" style="left:87px; top:902px;"><svg viewBox="0 0 18 26"><path d="M2 2 L16 13 L2 24 L7 13 Z" fill="var(--ring-orange)"/></svg>Sangria Tasting</p>
  <p class="activity" style="left:449px; top:902px;"><svg viewBox="0 0 18 26"><path d="M2 2 L16 13 L2 24 L7 13 Z" fill="var(--ring-orange)"/></svg>Iberian Ham</p>
  <p class="activity" style="left:87px; top:960px;"><svg viewBox="0 0 18 26"><path d="M2 2 L16 13 L2 24 L7 13 Z" fill="var(--ring-orange)"/></svg>Charcuteries &amp; Sherry Wine Tasting</p>
  <p class="activity" style="left:87px; top:1018px;"><svg viewBox="0 0 18 26"><path d="M2 2 L16 13 L2 24 L7 13 Z" fill="var(--ring-orange)"/></svg>Sailboat Experiences</p>
  <p class="activity" style="left:474px; top:1018px;"><svg viewBox="0 0 18 26"><path d="M2 2 L16 13 L2 24 L7 13 Z" fill="var(--ring-orange)"/></svg>Picnic Experiences</p>

  <p class="contact" style="left:107px; top:1106px;"><svg viewBox="0 0 22 22"><circle cx="11" cy="11" r="10" fill="var(--ring-orange)"/></svg>@coastalsupperroutescsr</p>
  <p class="contact" style="left:97px; top:1146px;"><svg viewBox="0 0 22 22"><path d="M5 2 L9 2 L10.5 7 L8 9 C9.5 12 10.5 13 13 14.5 L15 12 L20 13.5 L20 17.5 C20 19 19 20 17.5 20 C9 19.5 2.5 13 2 4.5 C2 3 3 2 5 2 Z" fill="var(--ring-orange)"/></svg>+34 600 12 34 56</p>
  <p class="contact" style="left:403px; top:1106px;"><svg viewBox="0 0 22 22"><rect x="1" y="4" width="20" height="14" rx="1.5" fill="var(--ring-orange)"/><path d="M2 5 L11 12.5 L20 5" fill="none" stroke="var(--poster-red)" stroke-width="1.8"/></svg>info@coastalsupperroutesnerja.example</p>
  <p class="contact" style="left:403px; top:1146px;"><svg viewBox="0 0 22 22"><circle cx="11" cy="11" r="9.5" fill="none" stroke="var(--ring-orange)" stroke-width="2.2"/><ellipse cx="11" cy="11" rx="4" ry="9.5" fill="none" stroke="var(--ring-orange)" stroke-width="2"/><line x1="1.5" y1="11" x2="20.5" y2="11" stroke="var(--ring-orange)" stroke-width="2"/></svg>www.coastalsupperroutesnerja.example</p>
</main>
</body>
</html>
```